Update the A4 Specials Page for Restaurant/Cafe

Provide a MINIMALIST attractive Specials page we can print weekly for our food and drink specials to give to our guests. Final design is to be provided in WORD Document so it can be easily edited by Manager. Should be black text and MINIMALIST to minimise ink usage as we print hundreds a week. We have UPLOADED the existing page as a template for you to update. Maybe logo can stay, see what you think. Or delete it and do something else. Keep it simple. Choose a good FONT. Could be a little playful with a cocktail ICON or something. Our existing menus can be seen at www.saltmeadowcafe.com.au and they are using font Alegreya. Please note we are unable to provide any feedback to designers, however we really do appreciate your time if you are submitting a design. Thank you for your participation.

```html
<!DOCTYPE html>
<html lang="en">
<head>
<meta charset="utf-8">
<title>Salt Meadow Cafe – Weekly Specials</title>
<link rel="stylesheet" href="https://fonts.googleapis.com/css2?family=Amatic+SC:wght@400;700&family=Chewy&display=swap">
<style>
  :root {
    --backdrop: #e9e6e1;
    --paper: #e4e2df;
    --ink: #262626;
    --ink-soft: #6b6b6b;
    --rule: #3a3a3a;
    --art-light: #efeeec;
    --art-mid: #c9c7c4;
  }
  * { box-sizing: border-box; margin: 0; padding: 0; }
  html, body { width: 1200px; height: 1100px; overflow: hidden; }
  body {
    background: var(--backdrop);
    display: flex; align-items: center; justify-content: center;
    font-family: "Amatic SC", cursive;
    color: var(--ink);
  }
  .specials-page {
    position: relative;
    width: 740px; height: 1046px;
    background: var(--paper);
    box-shadow: 0 6px 24px rgba(0,0,0,.18);
    overflow: hidden;
  }
  .brand {
    position: absolute; top: 50px; left: 0; right: 0;
    text-align: center;
    font-family: "Chewy", "Amatic SC", cursive;
    font-weight: 400;
    font-size: 64px; line-height: 1;
    color: var(--ink);
  }
  .brand-line { display: block; }
  .brand-line.small { font-size: 54px; margin-top: 4px; }
  .top-rule {
    position: absolute; top: 206px; left: 0; right: 0;
    border-top: 1px dotted var(--ink-soft);
  }
  .page-title {
    position: absolute; top: 222px; left: 0; right: 0;
    text-align: center;
    font-family: "Chewy", "Amatic SC", cursive;
    font-weight: 400;
    font-size: 58px; line-height: 1.1; letter-spacing: 1px;
  }
  .special {
    position: absolute;
    text-align: center;
  }
  .special-name {
    font-family: "Chewy", "Amatic SC", cursive;
    font-weight: 400;
    font-size: 32px; line-height: 1.15; color: #3b3b3b;
    letter-spacing: .5px;
  }
  .divider { display: block; margin: 4px auto 8px; }
  .special-desc { font-size: 25px; font-weight: 700; line-height: 1.15; }
  .special-note { font-size: 23px; color: var(--ink-soft); line-height: 1.15; }
  .special-abv { font-size: 19px; font-weight: 700; margin-top: 2px; }
  .price-badge {
    position: relative; display: block;
    width: 68px; height: 68px; margin: 10px auto 0;
  }
  .price-badge svg { position: absolute; inset: 0; }
  .price-badge span {
    position: absolute; inset: 0;
    display: flex; align-items: center; justify-content: center;
    font-family: "Chewy", "Amatic SC", cursive; font-size: 25px;
  }
  .special--filo { top: 308px; left: 60px; width: 620px; }
  .special--cocktail { top: 540px; left: 390px; width: 320px; }
  .special--soup { top: 610px; left: 40px; width: 320px; }
  .special--beer { top: 780px; left: 300px; width: 300px; }
  .cocktail-art {
    position: absolute; left: 0; right: 0; bottom: 0; height: 300px;
    background: linear-gradient(180deg, rgba(228,226,223,0) 0%, var(--art-light) 35%, var(--art-mid) 100%);
  }
</style>
</head>
<body>
  <main class="specials-page">
    <h1 class="brand">
      <span class="brand-line">Salt Meadow</span>
      <span class="brand-line small">Cafe</span>
    </h1>
    <div class="top-rule"></div>
    <h2 class="page-title">Weekly Specials</h2>

    <div class="cocktail-art" role="img" aria-label="Row of five outlined martini glass illustrations along the bottom of the page"></div>

    <section class="special special--filo">
      <h3 class="special-name">Chicken Filo</h3>
      <svg class="divider" width="200" height="14" viewBox="0 0 200 14"><line x1="0" y1="4" x2="200" y2="4" stroke="var(--rule)" stroke-width="1.5"/><line x1="20" y1="10" x2="180" y2="10" stroke="var(--rule)" stroke-width="1" stroke-dasharray="2 3"/></svg>
      <p class="special-desc">Creamy chicken with pinenuts, wrapped in filo pastry.</p>
      <p class="special-note">Served with side salad &amp; zulu sauce</p>
      <div class="price-badge">
        <svg viewBox="0 0 68 68"><circle cx="34" cy="34" r="31" fill="none" stroke="var(--ink)" stroke-width="2"/></svg>
        <span>$24</span>
      </div>
    </section>

    <section class="special special--cocktail">
      <h3 class="special-name">Cocktail Special</h3>
      <svg class="divider" width="200" height="14" viewBox="0 0 200 14"><line x1="0" y1="4" x2="200" y2="4" stroke="var(--rule)" stroke-width="1.5"/><line x1="20" y1="10" x2="180" y2="10" stroke="var(--rule)" stroke-width="1" stroke-dasharray="2 3"/></svg>
      <p class="special-desc">Vodka, passionfruit pulp, mango puree<br>top up with ginger &amp; lemon kombucha</p>
      <div class="price-badge">
        <svg viewBox="0 0 68 68"><circle cx="34" cy="34" r="31" fill="none" stroke="var(--ink)" stroke-width="2"/></svg>
        <span>$17</span>
      </div>
    </section>

    <section class="special special--soup">
      <h3 class="special-name">Minestrone Soup</h3>
      <svg class="divider" width="200" height="14" viewBox="0 0 200 14"><line x1="0" y1="4" x2="200" y2="4" stroke="var(--rule)" stroke-width="1.5"/><line x1="20" y1="10" x2="180" y2="10" stroke="var(--rule)" stroke-width="1" stroke-dasharray="2 3"/></svg>
      <p class="special-desc">Served with garlic bread</p>
      <div class="price-badge">
        <svg viewBox="0 0 68 68"><circle cx="34" cy="34" r="31" fill="none" stroke="var(--ink)" stroke-width="2"/></svg>
        <span>$8</span>
      </div>
    </section>

    <section class="special special--beer">
      <h3 class="special-name">Craft Beer Special</h3>
      <svg class="divider" width="200" height="14" viewBox="0 0 200 14"><line x1="0" y1="4" x2="200" y2="4" stroke="var(--rule)" stroke-width="1.5"/><line x1="20" y1="10" x2="180" y2="10" stroke="var(--rule)" stroke-width="1" stroke-dasharray="2 3"/></svg>
      <p class="special-desc">Copper Gecko<br>Orchard Ale</p>
      <p class="special-abv">4.8% Alc.</p>
      <div class="price-badge">
        <svg viewBox="0 0 68 68"><circle cx="34" cy="34" r="31" fill="var(--paper)" stroke="var(--ink)" stroke-width="2"/></svg>
        <span>$10</span>
      </div>
    </section>
  </main>
</body>
</html>
```